HearthMile business card and stationary design

We are looking for a simple yet elegant design for our mortgage company business card and stationary.

The card should include:
Name (Marcus Pell)
Title (CEO)
Phone Number (732-555-0182)
Address (48 Birchwell Court, Suite 314, Marlow Springs, NJ 07948)
Email (email@hearthmile.example)
"NMLS" i.e. (NMLS 61947)
"Company NMLS" (Company NMLS 274615)

Contact Information for Business Card

See above

```html
<!DOCTYPE html>
<html lang="en">
<head>
<meta charset="utf-8">
<title>HearthMile Business Card</title>
<link rel="stylesheet" href="https://fonts.googleapis.com/css2?family=Arimo:wght@400;700&display=swap">
<style>
  :root {
    --navy: #1b2633;
    --sky: #27a8e0;
    --paper: #ffffff;
    --ink: #1e1e1e;
    --backdrop: #2a2a2a;
  }
  * { margin: 0; padding: 0; box-sizing: border-box; }
  html, body { width: 1200px; height: 988px; overflow: hidden; }
  body {
    background: var(--backdrop);
    font-family: "Arimo", Arial, sans-serif;
    position: relative;
  }
  .card {
    position: absolute;
    width: 600px;
    height: 343px;
    border-radius: 3px;
    overflow: hidden;
  }
  .card-front {
    left: 50px; top: 70px;
    background: var(--navy);
    display: flex; align-items: center; justify-content: center;
  }
  .card-back {
    left: 550px; top: 520px;
    background: var(--paper);
  }
  .wordmark {
    font-family: "Arimo", Arial, sans-serif;
    font-weight: 700;
    font-size: 64px;
    letter-spacing: -1px;
    line-height: 1;
    white-space: nowrap;
  }
  .card-front .wordmark { color: var(--paper); }
  .card-back .wordmark {
    color: var(--navy);
    font-size: 44px;
    position: absolute;
    left: 0; right: 0; top: 40px;
    text-align: center;
  }
  .details {
    position: absolute;
    top: 128px; left: 0; right: 0;
    display: flex; justify-content: center;
  }
  .person {
    text-align: right;
    padding-right: 18px;
    padding-top: 26px;
    white-space: nowrap;
  }
  .person-name {
    color: var(--sky);
    font-weight: 700;
    font-size: 21px;
    letter-spacing: 0.3px;
    text-transform: uppercase;
  }
  .person-title, .person-license {
    color: var(--ink);
    font-size: 14px;
    margin-top: 3px;
  }
  .divider {
    width: 1px;
    height: 96px;
    background: var(--sky);
    margin-top: 8px;
  }
  .contact {
    padding-left: 18px;
    list-style: none;
    font-size: 14px;
    color: var(--ink);
    white-space: nowrap;
  }
  .contact li {
    display: flex; align-items: center; gap: 7px;
    height: 22px;
  }
  .contact svg { width: 12px; height: 12px; fill: var(--sky); flex: none; }
  .address-band {
    position: absolute;
    left: 0; right: 0; bottom: 28px;
    height: 34px;
    background: var(--navy);
    color: var(--paper);
    font-size: 14px;
    white-space: nowrap;
    display: flex; align-items: center; justify-content: center;
  }
</style>
</head>
<body>
  <section class="card card-front" aria-label="Card front">
    <div class="wordmark">HearthMile</div>
  </section>

  <section class="card card-back" aria-label="Card back">
    <div class="wordmark">HearthMile</div>

    <div class="details">
      <div class="person">
        <div class="person-name">Marcus Pell</div>
        <div class="person-title">CEO</div>
        <div class="person-license">Company NMLS 274615</div>
      </div>
      <div class="divider"></div>
      <ul class="contact">
        <li>NMLS 61947</li>
        <li>
          <svg viewBox="0 0 24 24" aria-hidden="true"><path d="M6.6 10.8a15.1 15.1 0 0 0 6.6 6.6l2.2-2.2c.3-.3.7-.4 1-.2 1.1.4 2.3.6 3.6.6.6 0 1 .4 1 1V20c0 .6-.4 1-1 1A17 17 0 0 1 3 4c0-.6.4-1 1-1h3.5c.6 0 1 .4 1 1 0 1.3.2 2.5.6 3.6.1.3 0 .7-.2 1z"/></svg>
          732-555-0182
        </li>
        <li>
          <svg viewBox="0 0 24 24" aria-hidden="true"><path d="M2 5h20v14H2z M2 5l10 8 10-8" fill="none" stroke="#27a8e0" stroke-width="2"/><path d="M2 6l10 8 10-8v13H2z"/></svg>
          email@hearthmile.example
        </li>
        <li>
          <svg viewBox="0 0 24 24" aria-hidden="true"><circle cx="12" cy="12" r="10" fill="none" stroke="#27a8e0" stroke-width="2"/><path d="M2 12h20M12 2c3 3 3 17 0 20M12 2c-3 3-3 17 0 20" fill="none" stroke="#27a8e0" stroke-width="1.6"/></svg>
          www.hearthmile.example
        </li>
      </ul>
    </div>

    <div class="address-band">48 Birchwell Court, Suite 314, Marlow Springs, NJ 07948</div>
  </section>
</body>
</html>
```